Logo + Label Design (Men’s Grooming Brand & Product Packaging)

Design a logo and 2 oz pomade label for Brel, a modern men’s grooming brand focused on clean, high-quality, natural ingredients. The design should establish a bold, masculine, minimalist identity that can later extend to products like shaving gel and body wash.

Key Requirements

Create a primary logo for “Brel” and a core label for the 2 oz pomade jar (screw-top).

Use a clean, modern style — masculine, confident, and approachable (think Dorran’s, Velta, Northfield Kit).

Design for 1–2 color screen printing on solid jar colors (white, black, or navy).

Avoid gradients, foil, or embossing. Must work in black & white.

Provide: vector logo, mockup of the 2 oz jar, color palette (CMYK/RGB/HEX), and font specs.

Winning design may lead to future projects (body wash, shave gel, skincare lines).

Font styles to use
Other font styles liked:
• We like the fonts and design concept in the attached mockup.

Requirements
Should not have
• We want to avoid too much writing or busy designs. We want to avoid having graphics/illustrations embedded in the logo if they will cause the brand to look less classy or sophisticated. We also want the design to look simple and all-American (e.g. Hollister and Vane, Pine Ledger, The KIM, etc). We’d like to give a Pellham & Royce vibe that feels classy and high end.

```html
<!DOCTYPE html>
<html lang="en">
<head>
<meta charset="utf-8">
<title>Brel Hair Pomade Label</title>
<link href="https://fonts.googleapis.com/css2?family=Playfair+Display:wght@400;700&family=Source+Serif+4:wght@400;600&display=swap" rel="stylesheet">
<style>
  :root {
    --page: #f0f0f0;
    --lid-rim: #58595b;
    --lid-face: #3a3b3d;
    --band: #161616;
    --ink-light: #dcdcdc;
    --ink-soft: #c9c9c9;
    --accent: #4a86b8;
    --rule: #9a9a9a;
  }
  * { box-sizing: border-box; margin: 0; padding: 0; }
  html, body { width: 1200px; height: 1200px; overflow: hidden; background: var(--page); }
  body { position: relative; font-family: "Source Serif 4", Georgia, serif; color: var(--ink-light); }

  /* Lid label */
  .lid {
    position: absolute; left: 66px; top: 355px; width: 520px; height: 520px;
    border-radius: 50%; background: var(--lid-rim);
  }
  .lid-face {
    position: absolute; left: 26px; top: 26px; width: 468px; height: 468px;
    border-radius: 50%; background: var(--lid-face);
  }
  .lid .side-title {
    position: absolute; left: 120px; top: 380px;
    transform: rotate(-90deg); transform-origin: left top;
    font-family: "Playfair Display", Georgia, serif; font-size: 21px; letter-spacing: .3px;
    white-space: nowrap; color: var(--ink-light);
  }
  .lid .divider { position: absolute; left: 172px; top: 138px; width: 1.5px; height: 258px; background: var(--ink-soft); }
  .lid .wordmark {
    position: absolute; left: 196px; top: 118px;
    font-family: "Playfair Display", Georgia, serif; font-weight: 700; font-size: 96px; line-height: 1;
    color: var(--ink-light); letter-spacing: -2px;
  }
  .lid .finish {
    position: absolute; left: 198px; top: 238px;
    font-family: "Playfair Display", Georgia, serif; font-weight: 700; font-size: 22px; line-height: 1.2;
  }
  .lid .scent {
    position: absolute; left: 198px; top: 314px;
    font-family: "Playfair Display", Georgia, serif; font-weight: 700; font-size: 24px; color: var(--accent);
  }
  .lid .net { position: absolute; left: 198px; top: 378px; font-size: 15px; }

  /* Wraparound side label, flattened */
  .band {
    position: absolute; left: 612px; top: 505px; width: 570px; height: 190px;
    background: var(--band);
  }
  .band .copy { position: absolute; left: 14px; top: 18px; width: 168px; font-size: 7.2px; line-height: 1.45; text-align: justify; color: var(--ink-soft); }
  .band .copy p + p { margin-top: 22px; }
  .band .copy b { font-weight: 600; }
  .band .rule { position: absolute; top: 20px; width: 1px; height: 150px; background: var(--rule); }
  .band .wordmark {
    position: absolute; left: 198px; top: 42px;
    font-family: "Playfair Display", Georgia, serif; font-weight: 700; font-size: 74px; line-height: 1;
    color: var(--ink-light); letter-spacing: -1.5px;
  }
  .band .side-title {
    position: absolute; left: 358px; top: 142px;
    transform: rotate(-90deg); transform-origin: left top;
    font-family: "Playfair Display", Georgia, serif; font-weight: 700; font-size: 11px; white-space: nowrap;
  }
  .band .finish { position: absolute; left: 378px; top: 30px; font-family: "Playfair Display", Georgia, serif; font-weight: 700; font-size: 11px; line-height: 1.2; }
  .band .scent { position: absolute; left: 378px; top: 72px; font-family: "Playfair Display", Georgia, serif; font-weight: 700; font-size: 11px; color: var(--accent); }
  .band .net { position: absolute; left: 378px; top: 148px; font-size: 7.5px; }
  .band .claims {
    position: absolute; left: 466px; top: 14px; width: 96px;
    border: 1px solid var(--rule); border-radius: 4px; padding: 4px 5px;
    list-style: none; font-size: 6.4px; line-height: 1.35; color: var(--ink-soft);
  }
  .band .claims li { position: relative; padding-left: 7px; margin-bottom: 3px; }
  .band .claims li:last-child { margin-bottom: 0; }
  .band .claims li::before { content: ""; position: absolute; left: 0; top: 3px; width: 3px; height: 3px; border-radius: 50%; background: var(--ink-light); }
  .band .maker { position: absolute; left: 468px; top: 124px; width: 96px; font-size: 5.2px; line-height: 1.4; color: var(--ink-soft); }
  .band .maker b { display: block; font-weight: 600; letter-spacing: .2px; }
  .band .maker .web { margin-top: 8px; }
</style>
</head>
<body>

  <section class="lid" aria-label="Jar lid label">
    <div class="lid-face">
      <div class="side-title">Hair Pomade</div>
      <div class="divider"></div>
      <div class="wordmark">brel</div>
      <div class="finish">Matte Finish<br>Medium Hold</div>
      <div class="scent">Fresh &amp; Clean</div>
      <div class="net">2 oz ( 57 g )</div>
    </div>
  </section>

  <section class="band" aria-label="Jar side label">
    <div class="copy">
      <p><b>DIRECTIONS:</b> Melt small amount of pomade between hands before massaging into damp hair (for sleeker look) or dry hair (for more texture). Style as desired. For external use only. Avoid contact with eyes. If irritation occurs, discontinue use.</p>
      <p><b>INGREDIENTS:</b> Butyrospermum Parkii (Shea Butter), Cera Alba (Beeswax), Polyglycerol-3 Beeswax (Cera Bellina), Caprylic/Capric Triglyceride (Fractionated Coconut Oil), Tocopherol (Vitamin E), Fragrance (Parfum)</p>
    </div>
    <div class="rule" style="left:189px"></div>
    <div class="wordmark">brel</div>
    <div class="rule" style="left:346px"></div>
    <div class="side-title">Hair Pomade</div>
    <div class="finish">Matte Finish<br>Medium Hold</div>
    <div class="scent">Fresh &amp; Clean</div>
    <div class="net">2 oz ( 57 g )</div>
    <ul class="claims">
      <li>Naturally derived plant</li>
      <li>Bee-based ingredients</li>
      <li>Alcohol Free</li>
      <li>Non-Irritating</li>
      <li>Formulated to minimize scalp irritation</li>
    </ul>
    <div class="maker">
      <b>MANUFACTURED BY:</b>
      Brel Health Products, Ashford, NC
      <div class="web">Visit Us At: brelgroomingco.com</div>
    </div>
  </section>

</body>
</html>
```